Interior Stylist business card design needed

I need a business card for my new company in Sydney called "Liv Harrowby Designs". The business offers an interior styling and colour consultancy. My clients are generally not very design savvy (hence why they use me) and can range from being quite conservative to really wanting something "out there". They can be looking for a budget makeover or something more expensive / substantial. I'd like my business card design to be stylish (but not overly formal). I certainly don't want it to be conservative. I'd like it to stand out a bit! I don't really have any aversion to particular colours and I don't have a logo as such - my business name is really all I have.

Target Market(s)

As above - home owners, ranging from conservative to modern

Industry/Entity Type

Conservative

Contact Information for Business Card

Liv Harrowby Designs
Colour consultancy and interior styling
ph: 0417 238 605
email: livharrowby@qoralnet.net.au

Requirements
Should not have
• Old fashioned writing or motifs. No Times Roman font!!

```html
<!DOCTYPE html>
<html lang="en">
<head>
<meta charset="utf-8">
<title>Liv Harrowby Designs – Business Card</title>
<link rel="stylesheet" href="https://fonts.googleapis.com/css2?family=Open+Sans:wght@300;700&display=swap">
<style>
  :root {
    --backdrop: #e9e9ea;
    --card-black: #000000;
    --ink-white: #ffffff;
    --paint-yellow: #e8c321;
    --paint-gold: #d6ad2c;
    --paint-orange: #d9652f;
    --paint-red: #e2512a;
    --paint-ochre: #c9a63a;
  }
  html, body {
    margin: 0;
    padding: 0;
    width: 1200px;
    height: 741px;
    overflow: hidden;
    background: var(--backdrop);
  }
  .canvas {
    position: relative;
    width: 1200px;
    height: 741px;
  }
  .business-card {
    position: absolute;
    left: 150px;
    top: 113px;
    width: 900px;
    height: 514px;
    background: var(--card-black);
    overflow: hidden;
    box-shadow: 0 10px 30px rgba(0, 0, 0, 0.18);
    font-family: "Open Sans", Arial, sans-serif;
    color: var(--ink-white);
  }
  .paint-swatch {
    position: absolute;
    top: 0;
    right: 0;
    width: 520px;
    height: 130px;
  }
  .company-name {
    position: absolute;
    left: 70px;
    top: 218px;
    margin: 0;
    font-weight: 700;
    font-size: 54px;
    letter-spacing: 0.5px;
    line-height: 1;
  }
  .tagline {
    position: absolute;
    left: 186px;
    top: 282px;
    margin: 0;
    font-weight: 300;
    font-size: 23px;
    line-height: 1;
  }
  .contact {
    position: absolute;
    left: 330px;
    top: 348px;
    margin: 0;
    font-weight: 300;
    font-size: 31px;
    line-height: 1;
  }
  .contact-phone { display: block; margin-bottom: 34px; }
  .contact-email { display: block; }
</style>
</head>
<body>
  <main class="canvas">
    <section class="business-card">
      <svg class="paint-swatch" viewBox="0 0 520 130" role="img" aria-label="Painted brush-stroke colour swatches in yellow, ochre, orange and red">
        <defs>
          <linearGradient id="swatchTones" x1="0" y1="0" x2="1" y2="0.4">
            <stop offset="0" stop-color="var(--paint-ochre)"/>
            <stop offset="0.35" stop-color="var(--paint-yellow)"/>
            <stop offset="0.6" stop-color="var(--paint-gold)"/>
            <stop offset="0.8" stop-color="var(--paint-orange)"/>
            <stop offset="1" stop-color="var(--paint-red)"/>
          </linearGradient>
        </defs>
        <rect x="0" y="0" width="520" height="130" fill="url(#swatchTones)"/>
      </svg>

      <h1 class="company-name">Liv Harrowby Designs</h1>
      <p class="tagline">Colour Consultancy &amp; Interior Styling</p>
      <p class="contact">
        <span class="contact-phone">0417 238 605</span>
        <span class="contact-email">livharrowby@qoralnet.net.au</span>
      </p>
    </section>
  </main>
</body>
</html>
```